Business card design needed

I need a business card design for a dog walking, dog minding and dog training business. Please refer to my website for the basic company colours and fonts I'm after. Planning on a double sided card, so all information doesn't need to be on the 'front' side.
Cheers

Industry/Entity Type

Dog Training

Contact Information for Business Card

Bramble Paws - gathering hounds
Rua 0498376214
bramblepaws.com.au
-walking
-holiday stays
-onsite care
-training and behavioural consultations

```html
<!DOCTYPE html>
<html lang="en">
<head>
<meta charset="utf-8">
<title>Bramble Paws – Business Card</title>
<link rel="stylesheet" href="https://fonts.googleapis.com/css2?family=Exo+2:ital,wght@0,300;1,300;1,700&display=swap">
<style>
  :root {
    --card-bg: #58595b;
    --ink-light: #ffffff;
    --accent: #e55a25;
    --art-top: #6a6b6d;
    --art-bottom: #606163;
  }
  * { margin: 0; padding: 0; box-sizing: border-box; }
  html, body {
    width: 1200px;
    height: 692px;
    overflow: hidden;
    background: var(--card-bg);
  }
  .card {
    position: relative;
    width: 1200px;
    height: 692px;
    background: var(--card-bg);
    color: var(--ink-light);
    font-family: "Exo 2", sans-serif;
    overflow: hidden;
  }
  .dog-artwork {
    position: absolute;
    left: 0;
    top: 30px;
    width: 310px;
    height: 662px;
    background: linear-gradient(180deg, var(--art-top), var(--art-bottom));
  }
  .mission {
    position: absolute;
    top: 26px;
    right: 45px;
    width: 680px;
    text-align: right;
    font-size: 40px;
    line-height: 58px;
    font-style: italic;
    font-weight: 300;
    letter-spacing: 0.2px;
  }
  .mission strong {
    font-weight: 700;
  }
  .brand-name {
    position: absolute;
    left: 322px;
    top: 470px;
    font-size: 104px;
    line-height: 1;
    font-weight: 300;
    text-transform: uppercase;
    letter-spacing: 2px;
    color: var(--ink-light);
    white-space: nowrap;
  }
  .brand-tagline {
    position: absolute;
    left: 326px;
    top: 598px;
    font-size: 44px;
    line-height: 1;
    font-weight: 300;
    color: var(--ink-light);
  }
</style>
</head>
<body>
  <main class="card">
    <div class="dog-artwork" role="img" aria-label="White line illustration of a standing dog in profile wearing an orange collar and lead"></div>

    <p class="mission">We’re about a <strong>good balance</strong> of <strong>fun,<br>exercise, proper stimulation</strong> and<br><strong>reinforcing good habits</strong> and<br><strong>canine manners</strong></p>

    <h1 class="brand-name">Bramble Paws</h1>
    <p class="brand-tagline">gathering hounds</p>
  </main>
</body>
</html>
```